Website design for legal tech start up in Switzerland (B2B)

We are for a legal tech start up in Switzerland called KOVA. We have been running since August 2016. This will be our first live website.

We need a website designed and business card design for our start-up in Switzerland. We also need the Web design to be converted into HTML and CSS files.

Function of website:
• To inform potential customers of our services
• Form a key part of our digital marketing and sales footprint.
• Branding

Please find attached logo.
Updates

Project Deadline Extended Reason: Giving us time to review submissions and provide opportunity for more submissions. Added Thursday, February 16, 2017

Project Deadline Extended
Reason: Looking for more idea's not necessarily set on blue and grey colours only.

Target Market(s)

B2B tech powered legal services.

Industry/Entity Type

Legal

Contact Information for Business Card

Lean and slick design.

Coding

Coded - Design and coding required

Number of Pages Required

5+ page

Requirements
Must have
• VERY LEAN AND CLEAN DESIGN!
• We have received many great standard designs, but we are looking for something more out-of-the box: You can get inspiration from these designs: http://www.pixelvane.com/websites/clean/
• Thanks!!
• Easy content management system
• Well structured coding for additional development
• Responsive webpage for all types of devices
• SEO optimized
• Tabs (Home, services, team, careers, blog, contact us)
• Colour scheme complementary to logo
Nice to have
• Look and Design - Approachable, High-tech, Modern
• Easy to add chat bot capability in future
Should not have
• Too busy/ too much clutter
• Not take to long to load

```html
<!DOCTYPE html>
<html lang="en">
<head>
<meta charset="utf-8">
<title>KOVA – Legal Tech</title>
<link rel="stylesheet" href="https://fonts.googleapis.com/css2?family=Montserrat:wght@500;600;700&family=Open+Sans:wght@400;600&family=Raleway:wght@500;600;800&display=swap">
<style>
:root{
  --navy:#1d3a6b;
  --navy-dark:#0f2a78;
  --hero-top:#13237a;
  --hero-mid:#3a3a6a;
  --hero-bottom:#5a4a32;
  --ink:#333;
  --heading:#555;
  --muted:#555;
  --soft-bg:#f5f5f5;
  --line:#e4e4e4;
  --footer:#3a3a3a;
  --white:#fff;
}
*{box-sizing:border-box;margin:0;padding:0}
html,body{width:813px;height:1200px;overflow:hidden;background:var(--white)}
body{position:relative;font-family:"Open Sans",sans-serif;color:var(--ink)}
a{color:inherit;text-decoration:none}

/* Hero */
.hero{position:absolute;left:0;top:0;width:813px;height:410px;
  background:linear-gradient(180deg,var(--hero-top) 0%,#26306e 25%,var(--hero-mid) 50%,#4a4048 72%,var(--hero-bottom) 100%)}
.hero-photo{position:absolute;inset:0;
  background:radial-gradient(ellipse at 50% 80%,rgba(230,170,70,.35),transparent 60%),
             radial-gradient(ellipse at 80% 45%,rgba(200,150,80,.3),transparent 50%)}
.topbar{position:absolute;left:0;top:0;width:813px;height:53px;background:rgba(10,25,110,.55)}
.brand{position:absolute;left:110px;top:14px;font-family:"Montserrat",sans-serif;font-weight:600;font-size:24px;letter-spacing:1px;color:var(--white)}
.nav{position:absolute;top:23px;left:0;font-family:"Montserrat",sans-serif;font-weight:600;font-size:8.5px;color:var(--white);letter-spacing:.2px}
.nav a{position:absolute;white-space:nowrap;transform:translateX(-50%)}
.nav .current::after{content:"";position:absolute;left:50%;top:29px;width:23px;height:2px;margin-left:-11.5px;background:var(--white)}
.nav-divider{position:absolute;left:680px;top:21px;width:1px;height:13px;background:rgba(255,255,255,.7)}
.search{position:absolute;left:693px;top:22px}
.hero-title{position:absolute;left:0;width:813px;top:192px;text-align:center;font-family:"Raleway",sans-serif;font-weight:800;font-size:29px;color:var(--white);letter-spacing:.3px}
.hero-text{position:absolute;left:0;width:813px;top:233px;text-align:center;font-family:"Raleway",sans-serif;font-weight:500;font-size:13.5px;line-height:18.5px;color:var(--white)}
.slide-arrow{position:absolute;top:204px;width:32px;height:48px;background:rgba(0,0,0,.35)}
.slide-arrow.prev{left:0}
.slide-arrow.next{right:0}

/* Features */
.features{position:absolute;left:0;top:410px;width:813px;height:137px;border-bottom:1px solid var(--line)}
.feature{position:absolute;top:45px;width:200px}
.feature svg{position:absolute;left:0;top:0}
.feature h3{position:absolute;left:55px;top:0;font-family:"Raleway",sans-serif;font-weight:500;font-size:12px;color:var(--ink);white-space:nowrap}
.feature p{position:absolute;left:55px;top:20px;width:130px;font-size:7.2px;line-height:12.5px;color:var(--muted)}

/* About */
.about{position:absolute;left:0;top:547px;width:813px;height:240px;background:var(--soft-bg);border-bottom:1px solid var(--line)}
.notch{position:absolute;left:397px;top:-1px}
.about h2{position:absolute;left:110px;top:36px;font-family:"Raleway",sans-serif;font-weight:600;font-size:21px;color:var(--heading)}
.about p{position:absolute;left:110px;top:70px;width:310px;font-size:7.2px;line-height:13.7px;color:var(--muted)}
.btn-solid{position:absolute;left:110px;top:175px;width:75px;height:27px;background:var(--navy);color:var(--white);font-family:"Montserrat",sans-serif;font-weight:600;font-size:7.5px;line-height:27px;text-align:center;border-radius:2px}
.about-photo{position:absolute;left:436px;top:42px;width:267px;height:156px;background:var(--white);padding:3px;box-shadow:0 0 3px rgba(0,0,0,.12)}
.about-photo div{width:100%;height:100%;background:linear-gradient(180deg,#2f7fd0 0%,#78b3e6 40%,#7a8a96 58%,#2fa0c8 75%,#1b8fb8 100%)}

/* Startup */
.startup{position:absolute;left:0;top:787px;width:813px;height:314px}
.startup h2{position:absolute;left:0;width:813px;top:22px;text-align:center;font-family:"Raleway",sans-serif;font-weight:600;font-size:21px;color:var(--heading)}
.card{position:absolute;top:71px;width:188px}
.card-photo{width:188px;height:104px}
.card h3{margin-top:12px;font-family:"Raleway",sans-serif;font-weight:500;font-size:12px;color:var(--ink)}
.card p{margin-top:9px;font-size:7.2px;line-height:12.8px;color:var(--muted)}
.btn-outline{display:block;margin-top:9px;width:66px;height:23px;border:1.5px solid var(--navy);border-radius:2px;color:var(--navy);font-family:"Montserrat",sans-serif;font-weight:600;font-size:7.5px;line-height:20px;text-align:center}

/* Footer */
.footer{position:absolute;left:0;top:1101px;width:813px;height:99px;background:var(--footer);color:var(--white);text-align:center}
.footer-brand{position:absolute;left:0;width:813px;top:19px;font-family:"Montserrat",sans-serif;font-weight:600;font-size:19px;letter-spacing:1px}
.footer-nav{position:absolute;left:0;width:813px;top:53px;font-family:"Montserrat",sans-serif;font-weight:500;font-size:7.2px}
.footer-nav span{margin:0 4px}
.copyright{position:absolute;left:0;width:813px;top:73px;font-size:6.8px}
</style>
</head>
<body>

<header class="hero">
  <div class="hero-photo" role="img" aria-label="Night view of a lakeside city with lit historic buildings, a tall fountain and reflections on the water"></div>
  <div class="topbar"></div>
  <div class="brand">KOVA</div>
  <nav class="nav">
    <a class="current" href="#" style="left:337px">HOME</a>
    <a href="#" style="left:397px">SERVICES</a>
    <a href="#" style="left:457px">TEAM</a>
    <a href="#" style="left:515px">CAREERS</a>
    <a href="#" style="left:574px">BLOG</a>
    <a href="#" style="left:640px">CONTACT US</a>
  </nav>
  <div class="nav-divider"></div>
  <svg class="search" width="10" height="10" viewBox="0 0 10 10" aria-label="Search"><circle cx="4" cy="4" r="3" fill="none" stroke="#fff" stroke-width="1.5"/><line x1="6.2" y1="6.2" x2="9" y2="9" stroke="#fff" stroke-width="1.6"/></svg>
  <h1 class="hero-title">WELCOME TO KOVA</h1>
  <p class="hero-text">Lorem ipsum dolor sit amet, consectetur adipiscing elit, sed do eiusmod<br>tem incididunt ut labore et dolore magna al ad minim veniamuis</p>
  <div class="slide-arrow prev"><svg width="32" height="48" viewBox="0 0 32 48"><polyline points="20,13 11,24 20,35" fill="none" stroke="#fff" stroke-width="1.5"/></svg></div>
  <div class="slide-arrow next"><svg width="32" height="48" viewBox="0 0 32 48"><polyline points="12,13 21,24 12,35" fill="none" stroke="#fff" stroke-width="1.5"/></svg></div>
</header>

<section class="features">
  <div class="feature" style="left:110px">
    <svg width="42" height="48" viewBox="0 0 42 48" fill="none" stroke="#1d3a6b" stroke-width="1.4">
      <rect x="1" y="1" width="30" height="40"/><rect x="5" y="4" width="30" height="40" fill="#fff"/><rect x="9" y="7" width="30" height="40" fill="#fff"/>
      <circle cx="24" cy="22" r="6"/><line x1="15" y1="37" x2="33" y2="37"/>
    </svg>
    <h3>Finibunorum</h3>
    <p>Cras mattis consectetur purus tlerm entu lomr ileo risus, porta acco ncur acvestibul mattis consectet umo.</p>
  </div>
  <div class="feature" style="left:312px">
    <svg width="56" height="48" viewBox="0 0 56 48" fill="none" stroke="#1d3a6b" stroke-width="1.4">
      <circle cx="16" cy="8" r="5"/><circle cx="28" cy="6" r="5"/><circle cx="40" cy="8" r="5"/>
      <path d="M6 38 V24 a8 8 0 0 1 16 0 V38"/><path d="M20 24 a8 8 0 0 1 16 0"/>
      <polyline points="28,34 36,42 54,22"/>
    </svg>
    <h3 style="left:63px">Finibunorum</h3>
    <p style="left:63px">Cras mattis consectetur purus tlerm entu lomr ileo risus, porta acco ncur acvestibul mattis consectet umo.</p>
  </div>
  <div class="feature" style="left:522px">
    <svg width="48" height="48" viewBox="0 0 48 48" fill="none" stroke="#1d3a6b" stroke-width="1.4">
      <rect x="10" y="4" width="34" height="36"/><line x1="14" y1="12" x2="40" y2="12"/><line x1="14" y1="20" x2="40" y2="20"/><line x1="14" y1="28" x2="40" y2="28"/>
      <line x1="2" y1="12" x2="14" y2="38"/>
    </svg>
    <h3 style="left:62px">Finibunorum</h3>
    <p style="left:62px">Cras mattis consectetur purus tlerm entu lomr ileo risus, porta acco ncur acvestibul mattis consectet umo.</p>
  </div>
</section>

<section class="about">
  <svg class="notch" width="20" height="10" viewBox="0 0 20 10"><polygon points="0,0 20,0 10,10" fill="#fff"/></svg>
  <h2>About Us</h2>
  <p>Sed ut perspiciatis unde omnis iste natus error sit voluptatem accusantium doloremque la udantium, totam rem aperiam, eaque ipsa quae ab illo inventore veritatis et quasi architecto beatae vitae dicta sunt expllcabo. Nemo enilorm ipsam voluptatem quia voluptas sit aspern atur autodit aut fugit, sed quia consequunturmagni dolores eos qui ratione voluptatem sei nesciuntque porro quisquam est, qui dolorem ipsum quia dolor sit amet, consectetur, adipi sci velit, sed quia non numquam eius modi tempora incidunt ut labore et dolore magnam aliqulorem quae rat voluptatemnim ad minima veniam, quis nostrum.</p>
  <a class="btn-solid" href="#">READ MORE</a>
  <div class="about-photo"><div role="img" aria-label="Lakeside house in front of snowy mountains reflected in clear turquoise water"></div></div>
</section>

<section class="startup">
  <h2>Legal Startup Company</h2>
  <article class="card" style="left:110px">
    <div class="card-photo" role="img" aria-label="Hands arranging colourful sticky notes and colour swatches on a wooden table" style="background:linear-gradient(135deg,#6b4a32,#c8b8a6 55%,#e7c9c8)"></div>
    <h3>Finibus Bonorum ealorum</h3>
    <p>Sed ut perspiciatis unde omnis iste natus errtlup tatem accusantium doloremque laudantium, tmem aperiam, eaque ipsa quae ab illo inventoreit.</p>
    <a class="btn-outline" href="#">READ MORE</a>
  </article>
  <article class="card" style="left:313px">
    <div class="card-photo" role="img" aria-label="A group of colleagues working together around a laptop" style="background:linear-gradient(135deg,#6a5a4a,#b9a58c 50%,#4a3a30)"></div>
    <h3>Finibus Bonorum ealorum</h3>
    <p>Sed ut perspiciatis unde omnis iste natus errtlup tatem accusantium doloremque laudantium, tmem aperiam, eaque ipsa quae ab illo inventoreit.</p>
    <a class="btn-outline" href="#">READ MORE</a>
  </article>
  <article class="card" style="left:515px">
    <div class="card-photo" role="img" aria-label="Overhead view of a team meeting with laptop, tablet and papers on a wooden desk" style="background:linear-gradient(135deg,#a0582e,#d8c7b3 50%,#8a4a28)"></div>
    <h3>Finibus Bonorum ealorum</h3>
    <p>Sed ut perspiciatis unde omnis iste natus errtlup tatem accusantium doloremque laudantium, tmem aperiam, eaque ipsa quae ab illo inventoreit.</p>
    <a class="btn-outline" href="#">READ MORE</a>
  </article>
</section>

<footer class="footer">
  <div class="footer-brand">KOVA</div>
  <nav class="footer-nav">HOME<span>|</span>SERVICES<span>|</span>TEAM<span>|</span>CAREERS<span>|</span>BLOG<span>|</span>CONTACT US</nav>
  <p class="copyright">© 2017 Kova. All Copyrights are reserved. Privacy Policy</p>
</footer>

</body>
</html>
```